Website & Logo The full package New Business new design and idea

Word Press

Simple, clean and very professional and approachable if possible

I am looking for a full business concept from logo to colour pallet and everything in between.
Brand new business concept, the successful applicant may continue on as our outsourced point person for all future work.

I will have an animated explainer video going over the four keys to business success Staff, Product & Services, Marketing, Sales and why the need a coach just like a sporting team to stay focused and clear on measurable outcomes.

Just added script (pdf attachment) i will be using for the explainer video at top of site.
Updates

Target Market(s)

Small business owners in Australia

Industry/Entity Type

Business Consultant

Number of Pages Required

1 page

Font styles to use
Sans Serif

Colors

Designer to choose colors to be used in the design.

Requirements
Must have
• Word press using Divi platform
• Ball park as per pdf uploaded
• Must work on all devices
• Social links
• Clear and straight forward movement through site
• Great capture of name and email,
• Free Download
• 10 Things you can start today in your small business to get you going again!
Nice to have
• clean one page potentially
• Free files and resources page
Should not have
• boring old menu and old framing

```html
<!DOCTYPE html>
<html lang="en">
<head>
<meta charset="utf-8">
<title>Bright Path Business Coach</title>
<link href="https://fonts.googleapis.com/css2?family=Roboto:wght@400;500;700&family=Lato:wght@400;700&display=swap" rel="stylesheet">
<style>
:root{
  --blue:#1565c0;
  --blue-bright:#1976e0;
  --blue-deep:#0b4a9a;
  --ink:#1f1f1f;
  --muted:#8a8a8a;
  --line:#ececec;
  --white:#ffffff;
}
*{box-sizing:border-box;margin:0;padding:0}
html,body{width:1200px;height:4357px;overflow:hidden;background:var(--white)}
body{position:relative;font-family:"Roboto",sans-serif;color:var(--ink)}
.abs{position:absolute}
.btn{position:absolute;display:flex;align-items:center;justify-content:center;background:var(--blue);color:var(--white);font:700 14px "Roboto",sans-serif;border-radius:22px;letter-spacing:.3px}
.para{font:400 13px/24px "Roboto",sans-serif;color:var(--muted)}
.h2{font:400 30px "Lato",sans-serif;color:var(--ink)}

/* header / hero */
.hero{top:0;left:0;width:1200px;height:592px;background:linear-gradient(100deg,#eef1f3 0%,#e4e8ea 38%,#9fb0c0 62%,#5d7290 78%,#dfe5e8 100%)}
.logo{left:110px;top:18px;font:700 24px "Roboto",sans-serif;color:var(--blue-bright);letter-spacing:-.3px}
.nav{top:25px;left:0;display:flex;font:500 13px "Roboto",sans-serif;color:var(--ink)}
.nav span{position:absolute;white-space:nowrap}
.hero-title{left:155px;top:176px;font:500 52px/58px "Roboto",sans-serif;color:var(--ink);white-space:nowrap}
.hero-title b{font-weight:500;color:var(--blue)}
.hero-sub{left:155px;top:302px;font:400 19px/25px "Roboto",sans-serif;color:var(--ink);width:450px}
.watch{left:350px;top:381px;display:flex;align-items:center;gap:12px;font:700 13px "Roboto",sans-serif;color:var(--blue)}

/* intro band */
.intro{top:592px;left:0;width:1200px;height:355px;background:linear-gradient(180deg,#1669cc,#0f5cb8);color:var(--white);text-align:center;font:400 13px/27px "Roboto",sans-serif;padding-top:76px}
.intro p{margin-bottom:16px}

/* photo slab */
.slab{position:absolute;width:488px;height:432px;border-radius:0 70px 70px 0;transform:skewY(-4deg)}
.slab.right{border-radius:70px 0 0 70px}

/* offer cards */
.card{position:absolute;background:var(--white);box-shadow:0 2px 14px rgba(0,0,0,.09);text-align:center}
.card h3{font:500 18px "Roboto",sans-serif;margin-top:38px}
.card .price{font:700 13px "Roboto",sans-serif;color:var(--blue);margin-top:12px}
.card ul{list-style:none;text-align:left;margin:24px 0 0 28px;width:260px}
.card li{position:relative;padding-left:29px;font:400 12.5px/23px "Roboto",sans-serif;color:var(--muted);margin-bottom:12px}
.card li svg{position:absolute;left:0;top:4px}

/* dark band */
.band{top:2496px;left:0;width:1200px;height:394px;background:linear-gradient(180deg,#0d4f9e,#0a4690);color:var(--white)}
.band-lead{position:absolute;top:64px;left:0;width:1200px;text-align:center;font:500 13px/29px "Roboto",sans-serif}
.band ul{position:absolute;top:158px;list-style:none;font:400 12.5px/28.5px "Roboto",sans-serif}
.band li{position:relative;padding-left:26px}
.band li::before{content:"";position:absolute;left:2px;top:12px;width:6px;height:6px;border-radius:50%;background:var(--white)}

/* about */
.about{top:3448px;left:0;width:1200px;height:363px;background:linear-gradient(180deg,#1a7ae6,#1668cf);color:var(--white);text-align:center}
.about h2{font:400 30px "Lato",sans-serif;margin-top:88px}
.about p{font:400 13px/26.5px "Roboto",sans-serif;margin-top:20px}

/* newsletter */
.field{position:absolute;left:653px;width:425px;height:42px;border-radius:21px;box-shadow:0 1px 8px rgba(0,0,0,.1);font:400 13px "Roboto",sans-serif;color:var(--muted);padding:13px 20px;background:var(--white)}

/* footer */
.foot-h{font:500 18px "Roboto",sans-serif;color:var(--blue)}
.foot-l{font:400 13px/26px "Roboto",sans-serif;color:var(--muted)}
</style>
</head>
<body>

<header class="abs hero">
  <div class="abs" style="left:600px;top:0;width:520px;height:592px;background:linear-gradient(180deg,#6d84a1,#2c4a78)" role="img" aria-label="Photo of an excited businessman in a blue shirt celebrating in an office"></div>
  <div class="abs" style="left:0;top:230px;width:260px;height:362px;background:linear-gradient(180deg,#c9d2c6,#8fa46c)" role="img" aria-label="Office desk with clock and potted plant"></div>
  <div class="abs logo">BRIGHT PATH BUSINESS COACH</div>
  <nav class="abs nav">
    <span style="left:538px">HOME</span>
    <span style="left:623px">ABOUT US</span>
    <span style="left:735px">SERVICES</span>
    <span style="left:846px">CAREER</span>
    <span style="left:942px">CONTACT US</span>
    <span style="left:1075px"><svg width="13" height="13" viewBox="0 0 13 13"><circle cx="5.5" cy="5.5" r="4" fill="none" stroke="#1f1f1f" stroke-width="2"/><path d="M8.5 8.5l3.5 3.5" stroke="#1f1f1f" stroke-width="2"/></svg></span>
  </nav>
  <h1 class="abs hero-title">Bright Path <b>Business<br>Coach</b></h1>
  <p class="abs hero-sub">10 Things you can start today in your small business to get you going again!</p>
  <div class="btn" style="left:155px;top:376px;width:168px;height:39px">CONTACT US</div>
  <div class="abs watch">
    <svg width="34" height="34" viewBox="0 0 34 34"><circle cx="17" cy="17" r="15" fill="#fff" stroke="#1565c0" stroke-width="2"/><path d="M14 11l9 6-9 6z" fill="#1565c0"/></svg>
    Watch Video
  </div>
</header>

<section class="abs intro">
  <p>Bright Path Business Coach is here to help, support and turn your small business around, It may not be easy, it may not be pretty,<br>it may not be conventional or what you want to hear but my only goal is to help you succeed in your small business struggling in Australia</p>
  <p>I offer a 12 week fully supported and personally applied program, each week you complete the activities and we<br>meet over video call where your actions are accountable and measurable.</p>
  <p>Every business and small business owner are different, so not one solution fits all, and that's exactly why I can<br>make it personal for those who want to change and need it to happen now..</p>
</section>

<section>
  <div class="slab" style="left:0;top:1022px;background:linear-gradient(135deg,#d8dbe0,#9aa3ae 60%,#c7b9a6)" role="img" aria-label="Photo of a team meeting around a laptop showing charts"></div>
  <h2 class="abs" style="left:625px;top:1082px;font:400 29px 'Lato',sans-serif">Australian Small Business Snapshot</h2>
  <div class="abs" style="left:625px;top:1122px;font:400 12.5px 'Roboto',sans-serif;color:var(--blue)">Nov 26, 2018</div>
  <p class="abs para" style="left:625px;top:1160px;width:445px">It's an extremely sad sign of the times when you're confronted with a myriad of 'for lease' signs in shop windows along major shopping hubs.</p>
  <p class="abs para" style="left:625px;top:1228px;width:445px">While most businesses in Australia are small -- accounting for 97 percent of all businesses -- they're shutting their doors in alarmingly high numbers.</p>
  <div class="btn" style="left:625px;top:1340px;width:143px;height:40px">READ MORE</div>
</section>

<section>
  <h2 class="abs h2" style="left:0;top:1496px;width:1200px;text-align:center">Get Offer</h2>
  <svg width="0" height="0" style="position:absolute"><defs><symbol id="tick" viewBox="0 0 14 14"><circle cx="7" cy="7" r="7" fill="#1565c0"/><path d="M3.8 7.2l2.2 2.2 4.2-4.4" fill="none" stroke="#fff" stroke-width="1.8"/></symbol></defs></svg>

  <div class="card" style="left:112px;top:1583px;width:303px;height:357px">
    <h3>GIVING BACK FREE</h3><div class="price">3 months</div>
    <ul>
      <li><svg width="14" height="14"><use href="#tick"/></svg>Bright Path Business Coach is offering 4 FREE 12-week</li>
      <li><svg width="14" height="14"><use href="#tick"/></svg>Just fill out the information sheet and we will let you know as soon as possible.</li>
      <li><svg width="14" height="14"><use href="#tick"/></svg>Maybe show the 12 free placements</li>
    </ul>
    <div class="btn" style="left:96px;top:278px;width:124px;height:38px">SIGN IN</div>
  </div>
  <div class="card" style="left:786px;top:1583px;width:302px;height:357px">
    <h3>JUST A BIT MORE</h3><div class="price">$400 a week for 12 weeks</div>
    <ul>
      <li><svg width="14" height="14"><use href="#tick"/></svg>Bright Path Business Coach is offering 4 FREE 12-week</li>
      <li><svg width="14" height="14"><use href="#tick"/></svg>Just fill out the information sheet and we will let you know as soon as possible.</li>
      <li><svg width="14" height="14"><use href="#tick"/></svg>Maybe show the 4 free placements</li>
    </ul>
    <div class="btn" style="left:84px;top:278px;width:124px;height:38px">SIGN IN</div>
  </div>
  <div class="card" style="left:418px;top:1555px;width:364px;height:414px;box-shadow:0 4px 20px rgba(0,0,0,.12)">
    <h3 style="margin-top:66px">SPECIAL OFFER</h3><div class="price">$200 a week for 12 weeks</div>
    <ul style="margin-left:45px">
      <li><svg width="14" height="14"><use href="#tick"/></svg>Bright Path Business Coach is offering 4 FREE 12-week</li>
      <li><svg width="14" height="14"><use href="#tick"/></svg>Just fill out the information sheet and we will let you know as soon as possible.</li>
      <li><svg width="14" height="14"><use href="#tick"/></svg>Maybe show the 12 free placements</li>
    </ul>
    <div class="btn" style="left:121px;top:306px;width:124px;height:38px">SIGN IN</div>
  </div>
</section>

<section>
  <h2 class="abs h2" style="left:110px;top:2118px">How it works</h2>
  <p class="abs para" style="left:110px;top:2172px;width:470px">With your permission I breakdown your business, Staff, Products / Services, Marketing and Sales.</p>
  <p class="abs para" style="left:110px;top:2238px;width:470px">Under each of these four key components are up to 30 or more components including your staff training and experience, business financials, public exposure and engagement with target market, current marketing and processes required to make income</p>
  <div class="slab right" style="left:718px;top:2020px;width:482px;height:420px;background:linear-gradient(135deg,#1f3e6e,#3a6ca8 55%,#c9ccd1)" role="img" aria-label="Photo of hands typing on a laptop with idea, planning, start up company and marketing tags"></div>
</section>

<section class="abs band">
  <p class="band-lead">Regardless if you're a Bright Path Business Coach Free, Special Offer or Just a Bit More, Small Business Owner you all get one on one direct access to me each<br>week along with mountains of accountable activities to turn your small business around into the dream you had hoped it could be.</p>
  <ul style="left:110px;width:460px">
    <li>Getting a measurable base line of the financials and existing marketing.</li>
    <li>Discussing the past ups and downs and looking forward to the future</li>
    <li>Understanding your product or service and how it fits into the<br>current marketplace.</li>
    <li>Looking into the staff for potential opportunities or training.</li>
    <li>Understanding market trends and embracing a SWOT analysis</li>
  </ul>
  <ul style="left:610px;width:500px">
    <li>Looking to establish a mastermind local group with a successful business</li>
    <li>Partnership opportunities</li>
    <li>Creating and applying marketing objectives</li>
    <li>How to give more to grow</li>
    <li>External learning materials applied as per needs such as specific</li>
  </ul>
  <div class="abs" style="left:610px;top:300px;font:400 12.5px 'Roboto',sans-serif">podcast episodes or suggested books that relate to a special need to be supported.</div>
</section>

<section>
  <div class="slab" style="left:0;top:2946px;background:linear-gradient(135deg,#6b4a33,#8d6a4e 50%,#4a3324)" role="img" aria-label="Photo of a wooden desk with laptop, coffee, glasses and phone seen from above with network icons"></div>
  <h2 class="abs h2" style="left:625px;top:3008px">Application</h2>
  <p class="abs para" style="left:625px;top:3070px;width:445px">Placements are strictly limited to 28 per quarter as they are all managed personally for the best possible</p>
  <p class="abs para" style="left:625px;top:3140px;width:445px">You must have internet access, put the time aside between 1-2 hours a week on video call and be open to change and motivated and accountable to succeed with every scheduled meeting.</p>
  <div class="btn" style="left:625px;top:3268px;width:177px;height:40px">FREE DOWNLOAD</div>
</section>

<section class="abs about">
  <div class="abs" style="left:0;top:0;width:1200px;height:363px;background:radial-gradient(ellipse at 50% 40%,rgba(255,255,255,.08),rgba(0,0,0,0) 60%)" role="img" aria-label="Faint photo of a smiling coach behind the blue overlay"></div>
  <h2 style="position:relative">About Me</h2>
  <p style="position:relative">I am not superman, I just found myself absorbing information over the past 10 years through some mentors and<br>personal development and see so many small business owners struggling and I got sick of telling myself how I would change things that I<br>eventually approached some businesses for free and asked if they needed a hand and they were over the moon, very receptive and after a 1 hour<br>talk the immediate action taken saw some massive returns exceeding even my estimates and now I just want to help more Small Business<br>Owners through Bright Path Business Coach support.</p>
</section>

<section>
  <h2 class="abs" style="left:110px;top:3897px;font:400 28px/38px 'Lato',sans-serif">Let's Talk &amp;<br>Subscribe Our Newsletter</h2>
  <p class="abs para" style="left:110px;top:3990px;width:470px">Lorem ipsum dolor sit amet, consectetur adipiscing elit, sed do eiusmod tempor incididunt ut labore et dolore magna aliqua. Ut enim ad minim</p>
  <div class="field" style="top:3910px">Name</div>
  <div class="field" style="top:3960px">Email</div>
  <div class="btn" style="left:655px;top:4016px;width:120px;height:36px;font-size:12px">SUBSCRIBE</div>
</section>

<footer>
  <div class="abs foot-h" style="left:110px;top:4120px">General Info</div>
  <div class="abs foot-l" style="left:110px;top:4152px;width:270px;text-decoration:underline">10 Things you can start today in your small business to get you going again!</div>
  <div class="abs" style="left:110px;top:4230px;display:flex;gap:20px">
    <svg width="12" height="12"><circle cx="6" cy="6" r="5" fill="#9a9a9a"/></svg>
    <svg width="12" height="12"><circle cx="6" cy="6" r="5" fill="#9a9a9a"/></svg>
    <svg width="12" height="12"><circle cx="6" cy="6" r="5" fill="#9a9a9a"/></svg>
    <svg width="12" height="12"><circle cx="6" cy="6" r="5" fill="#9a9a9a"/></svg>
  </div>
  <div class="abs foot-h" style="left:672px;top:4120px">Quick Links</div>
  <div class="abs foot-l" style="left:672px;top:4155px">Home<br>About Us<br>Services<br>Career<br>Contact Us</div>
  <div class="abs foot-h" style="left:903px;top:4120px">Importance</div>
  <div class="abs foot-l" style="left:903px;top:4155px">Faq<br>Privacy Policy<br>Terms &amp; Conditions</div>
  <div class="abs" style="left:0;top:4325px;width:1200px;text-align:center;font:400 11px 'Roboto',sans-serif;color:var(--muted)">©Copyright 2018 Bright Path Business Coach All Rights Reserved</div>
</footer>

</body>
</html>
```